Business Cards Needed for Innovative Healthcare Marketing Company

We are a marketing company focused on healthcare. Our company is all about rebranding yourself renewing your image and generating results. The phoenix stands for "reborn" or "rising" which we provide new brands for our clients we take their old brands and renew it with creativity and innovation. I am looking for a business card with color dimension. I have attached an example of a card I think has the look and feel of what I am trying to accomplish. I like that the card example has black and grey font colors, I like the font placement and the small logo, I really like the use of the colors on the right those are the colors of my logo. My logo is phoenix so maybe incorporating flames similar to that design. I would like the back a solid color maybe red with an opaque version of the logo and website. As a marketing company I am always open to creative liberty!

Target Market(s)

Doctors and business professionals.

Industry/Entity Type

Marketing

Contact Information for Business Card

Valcorne Health Care Marketing
Marla Tenwick- CEO
#(512)638-2974
email-marla@valcorne.com
website- valcorne.com

Font styles to use
Sans Serif

Colors
ec1f27
f37122
ffc214
fbed22
fbf289
f04a50

Requirements
Must have
• The logo and required information
Nice to have
• icons by the information
Should not have
• child like font

```html
<!DOCTYPE html>
<html lang="en">
<head>
<meta charset="utf-8">
<title>Valcorne Health Care Marketing – Business Cards</title>
<link rel="stylesheet" href="https://fonts.googleapis.com/css2?family=Montserrat:wght@400;500;700&display=swap">
<style>
  :root {
    --canvas: #e9e7e4;
    --card: #ffffff;
    --brand-red: #a5242a;
    --brand-orange: #f37122;
    --brand-gold: #f7a21b;
    --name-gold: #f5a623;
    --logo-rose: #b8323a;
    --text-light: #ffffff;
  }
  * { box-sizing: border-box; margin: 0; padding: 0; }
  html, body {
    width: 1200px; height: 900px; overflow: hidden;
    background: var(--canvas);
    font-family: "Montserrat", sans-serif;
  }
  .stage { position: relative; width: 1200px; height: 900px; }
  .card {
    position: absolute; left: 280px; width: 640px; height: 366px;
    background: var(--card); border-radius: 26px; overflow: hidden;
    box-shadow: 0 14px 30px rgba(0,0,0,0.18);
  }
  .card--back { top: 60px; }
  .card--front { top: 474px; }

  /* Back */
  .back-mark {
    position: absolute; left: 200px; top: 120px;
    display: flex; align-items: center; gap: 14px;
  }
  .mark-dot {
    width: 34px; height: 34px; border-radius: 50%;
    background: var(--brand-orange);
  }
  .back-mark .brand-name {
    font-size: 34px; font-weight: 400; letter-spacing: 3px; color: var(--logo-rose);
  }
  .back-web {
    position: absolute; right: 30px; bottom: 30px;
    font-size: 15px; font-weight: 500; color: var(--logo-rose);
  }

  /* Front */
  .red-band { position: absolute; inset: 0; width: 640px; height: 366px; }
  .front-logo {
    position: absolute; left: 46px; top: 62px;
    display: flex; align-items: center; gap: 14px;
  }
  .front-logo .brand-name {
    font-size: 34px; font-weight: 400; letter-spacing: 3px;
    color: var(--logo-rose); line-height: 1.05;
  }
  .front-logo .brand-name small {
    display: block; font-size: 13px; letter-spacing: 2px; margin-top: 6px;
    padding-top: 6px; border-top: 1px solid var(--logo-rose);
  }
  .person { position: absolute; left: 80px; top: 214px; }
  .person-name {
    font-size: 22px; font-weight: 700; color: var(--name-gold); letter-spacing: 1px;
  }
  .person-title { font-size: 15px; color: var(--text-light); margin-top: 2px; }
  .contact-list { list-style: none; margin-top: 12px; }
  .contact-list li {
    display: flex; align-items: center; gap: 10px;
    font-size: 16px; color: var(--text-light); margin-bottom: 5px;
  }
  .contact-list svg { width: 13px; height: 13px; flex: none; }
</style>
</head>
<body>
<main class="stage">

  <section class="card card--back" aria-label="Card back">
    <div class="back-mark">
      <span class="mark-dot"></span>
      <span class="brand-name">VALCORNE</span>
    </div>
    <p class="back-web">www.valcorne.com</p>
  </section>

  <section class="card card--front" aria-label="Card front">
    <svg class="red-band" viewBox="0 0 640 366" aria-hidden="true">
      <polygon points="0,205 640,110 640,366 0,366" fill="var(--brand-red)"/>
    </svg>

    <div class="front-logo">
      <span class="mark-dot"></span>
      <span class="brand-name">VALCORNE<small>HEALTH CARE MARKETING</small></span>
    </div>

    <div class="person">
      <h1 class="person-name">MARLA TENWICK</h1>
      <p class="person-title">CEO</p>
      <ul class="contact-list">
        <li>
          <svg viewBox="0 0 24 24" aria-hidden="true"><path fill="var(--brand-gold)" d="M6.6 10.8a15.1 15.1 0 0 0 6.6 6.6l2.2-2.2a1 1 0 0 1 1-.25 11.4 11.4 0 0 0 3.6.57 1 1 0 0 1 1 1V20a1 1 0 0 1-1 1A17 17 0 0 1 3 4a1 1 0 0 1 1-1h3.5a1 1 0 0 1 1 1c0 1.25.2 2.45.57 3.6a1 1 0 0 1-.25 1z"/></svg>
          (512)638-2974
        </li>
        <li>
          <svg viewBox="0 0 24 24" aria-hidden="true"><rect x="2" y="5" width="20" height="14" rx="2" fill="none" stroke="var(--brand-gold)" stroke-width="2.4"/><path d="M3 6l9 7 9-7" fill="none" stroke="var(--brand-gold)" stroke-width="2.4"/></svg>
          marla@valcorne.com
        </li>
        <li>
          <svg viewBox="0 0 24 24" aria-hidden="true"><circle cx="12" cy="12" r="10" fill="var(--brand-gold)"/><path d="M2 12h20M12 2c3 3 3 17 0 20M12 2c-3 3-3 17 0 20" fill="none" stroke="var(--brand-red)" stroke-width="1.4"/></svg>
          www.valcorne.com
        </li>
      </ul>
    </div>
  </section>

</main>
</body>
</html>
```